Brand new redesign of Brightpath finance website

I need a new website design that i can advertise a great low interest rate on the front page and capture input application details that will send through to my email address.

some car finance companies will be similar to this would be listed below

tallowcredit.example.com.au
mirabelfinance.example.com.au
finance725.example.com.au
quenbyfinance.example.com.au
finance91.example.com.au

Reason: I have changed the project to a committed project. all the webpages should have the same format just different content and i want to be able to edit the front page easily to update my interest rates.

Target Market(s)

Australian Finance market targeting a younger demographic

Industry/Entity Type

Finance

Coding

Coded - Design and coding required

Number of Pages Required

5+ page

Font styles to use
Serif
Sans Serif

Colors
0255a3
ffffff
cedeed

Requirements
Must have
• application capture form
• apply now buttons
• Headline rate front page

```html
<!DOCTYPE html>
<html lang="en">
<head>
<meta charset="utf-8">
<title>Brightpath Finance – Application Form</title>
<link href="https://fonts.googleapis.com/css2?family=Lato:wght@400;700;900&family=Poppins:wght@500&display=swap" rel="stylesheet">
<style>
:root{
  --brand:#0255a3;
  --brand-dark:#01468a;
  --brand-light:#4f86d6;
  --pale:#cedeed;
  --white:#ffffff;
  --header:#231f20;
  --ink:#2b2b2b;
  --muted:#555555;
  --border:#c9ccd0;
  --rule:#d5d8dc;
  --req:#e0161b;
}
*{box-sizing:border-box;margin:0;padding:0}
html,body{width:1200px;height:2521px;overflow:hidden;background:var(--white)}
body{position:relative;font-family:"Lato",sans-serif;color:var(--ink)}
.abs{position:absolute}

/* top bars */
.top-strip{left:0;top:0;width:1200px;height:34px;background:var(--brand)}
.apply-tab{left:946px;top:0;width:121px;height:34px;background:var(--pale);display:flex;align-items:center;justify-content:center;gap:8px;font-size:12.5px;color:var(--brand)}
.site-header{left:0;top:34px;width:1200px;height:117px;background:var(--header)}
.brand-name{left:133px;top:80px;font-size:21px;font-weight:700;color:var(--brand-light);line-height:26px;white-space:nowrap}
.header-phone{left:823px;top:60px;display:flex;align-items:center;gap:8px;color:var(--white);font-size:15px}
.social{display:flex;gap:9px}
.social span{display:block;width:27px;height:27px;border-radius:3px;background:#2a6fc2}
.header-social{left:970px;top:58px}
.nav{left:333px;top:106px;display:flex;align-items:center;height:28px}
.nav a{color:var(--white);text-decoration:none;font-size:13px;font-weight:700;letter-spacing:.2px;margin-right:21px;line-height:28px}
.nav a.active{background:var(--brand);padding:0 14px;margin-right:18px}

/* hero */
.hero{left:0;top:151px;width:1200px;height:232px;background:
  radial-gradient(ellipse 420px 170px at 690px 110px,rgba(255,226,150,.95),rgba(255,160,50,.6) 45%,rgba(255,120,20,0) 75%),
  linear-gradient(90deg,#6e0d10 0%,#b31b1f 18%,#d93a26 35%,#f08a2e 52%,#c8712c 70%,#5a3a22 88%,#2b1e18 100%)}
.hero-title{right:133px;top:246px;font-size:47px;font-weight:900;color:var(--white);letter-spacing:.5px;text-shadow:0 2px 6px rgba(0,0,0,.45)}

/* form */
.section-title{font-family:"Poppins",sans-serif;font-weight:500;font-size:26px;line-height:34px;color:var(--brand)}
.section-rule{height:1px;background:var(--rule)}
.label{font-size:14.5px;font-weight:700;color:var(--ink);line-height:18px;white-space:nowrap}
.req{color:var(--req)}
.field{height:39px;border:1.5px solid var(--border);border-radius:5px;background:var(--white);font-size:14.5px;color:var(--muted);line-height:36px;padding-left:15px}
.field svg{position:absolute;right:14px;top:13px}
.unit{font-size:14.5px;font-weight:700;color:var(--ink);line-height:18px}
.agree{left:336px;top:2111px;display:flex;align-items:center;gap:12px;font-size:14.5px;font-weight:700;color:var(--ink)}
.checkbox{width:33px;height:34px;border:1.5px solid var(--border);border-radius:4px;display:flex;align-items:center;justify-content:center}
.agree a{color:var(--brand);text-decoration:underline}
.submit{left:454px;top:2175px;width:292px;height:58px;border-radius:6px;background:linear-gradient(180deg,#1a6fc0,var(--brand) 55%,var(--brand-dark));border:1px solid #013f7c;color:var(--white);font-size:23px;font-weight:700;letter-spacing:3px;display:flex;align-items:center;justify-content:center}

/* footer */
.footer-info{left:0;top:2302px;width:1200px;height:135px;background:var(--pale)}
.footer-icon{width:33px;height:33px;border-radius:50%;background:var(--brand);display:flex;align-items:center;justify-content:center}
.footer-head{font-size:14px;font-weight:700;color:var(--ink);line-height:18px;white-space:nowrap}
.footer-text{font-size:14px;color:var(--ink);line-height:18px;margin-top:8px;white-space:nowrap}
.footer-divider{width:1px;height:101px;background:#b9c9da}
.footer-bar{left:0;top:2437px;width:1200px;height:84px;background:var(--brand)}
.footer-nav{left:133px;top:2457px;display:flex;gap:14px}
.footer-nav a{color:var(--white);text-decoration:none;font-size:11.5px;font-weight:700}
.copyright{left:133px;top:2484px;color:var(--white);font-size:11.5px;font-weight:700}
.footer-social{left:970px;top:2466px}
</style>
</head>
<body>

<div class="abs top-strip"></div>
<div class="abs apply-tab">
  <svg width="14" height="16" viewBox="0 0 14 16"><path d="M1 1h8l4 4v10H1z" fill="none" stroke="#333" stroke-width="1.4"/><path d="M4 7h6M4 10h6M4 13h4" stroke="#333" stroke-width="1.2"/></svg>
  Apply Now
</div>

<header class="abs site-header"></header>
<div class="abs brand-name">Brightpath Finance</div>
<div class="abs header-phone">
  <svg width="20" height="20" viewBox="0 0 20 20"><path d="M5 2l3 4-2 2c1 2 3 4 5 5l2-2 4 3-2 3C8 17 3 12 2 5z" fill="none" stroke="#fff" stroke-width="1.4" stroke-linejoin="round"/></svg>
  1300 555 018
</div>
<div class="abs social header-social"><span></span><span></span><span></span></div>
<nav class="abs nav">
  <a class="active">HOME</a><a>ABOUT</a><a>VEHICLE LOANS</a><a>OTHER LOANS</a><a>INSURANCE</a><a>FINANCE CALCULATOR</a><a>CONTACT</a>
</nav>

<div class="abs hero" role="img" aria-label="Photo of a red car's side mirror speeding along a road at sunset with motion blur"></div>
<h1 class="abs hero-title">APPLICATION FORM</h1>

<!-- Loan details -->
<h2 class="abs section-title" style="left:134px;top:430px">Loan Details</h2>
<div class="abs section-rule" style="left:319px;top:450px;width:748px"></div>
<div class="abs label" style="left:133px;top:495px">How Much Are You Looking To Borrow? (approx.): <span class="req">*</span></div>
<div class="abs label" style="left:637px;top:495px">Purpose Of Loan:</div>
<div class="abs field" style="left:133px;top:528px;width:475px">30,000</div>
<div class="abs field" style="left:637px;top:528px;width:430px">Car<svg width="14" height="9" viewBox="0 0 14 9"><path d="M1 1l6 6 6-6" fill="none" stroke="#666" stroke-width="1.6"/></svg></div>
<div class="abs label" style="left:133px;top:588px">How Much Could You Repay Weekly? (approx.): <span class="req">*</span></div>
<div class="abs field" style="left:133px;top:622px;width:475px">30,000</div>

<!-- Applicant details -->
<h2 class="abs section-title" style="left:132px;top:701px">Applicant Details</h2>
<div class="abs section-rule" style="left:378px;top:721px;width:689px"></div>
<div class="abs label" style="left:133px;top:767px">Title:</div>
<div class="abs label" style="left:455px;top:767px">First Name: <span class="req">*</span></div>
<div class="abs label" style="left:778px;top:767px">Last Name: <span class="req">*</span></div>
<div class="abs field" style="left:133px;top:800px;width:288px">Mr.</div>
<div class="abs field" style="left:455px;top:800px;width:290px"></div>
<div class="abs field" style="left:778px;top:800px;width:289px"></div>

<div class="abs label" style="left:133px;top:862px">No. Of Dependants:</div>
<div class="abs label" style="left:455px;top:862px">Drivers License Number: <span class="req">*</span></div>
<div class="abs label" style="left:778px;top:862px">Date Of Birth: <span class="req">*</span></div>
<div class="abs field" style="left:133px;top:894px;width:288px"></div>
<div class="abs field" style="left:455px;top:894px;width:290px">2</div>
<div class="abs field" style="left:778px;top:894px;width:289px"><svg width="16" height="15" viewBox="0 0 16 15" style="top:11px"><rect x="1" y="2" width="14" height="12" fill="none" stroke="#888" stroke-width="1.2"/><path d="M1 5h14M5 8h1M8 8h1M11 8h1M5 11h1M8 11h1M11 11h1M5 0v3M11 0v3" stroke="#888" stroke-width="1.2"/></svg></div>

<div class="abs label" style="left:133px;top:954px">Contact Number:</div>
<div class="abs label" style="left:455px;top:954px">Email Address: <span class="req">*</span></div>
<div class="abs label" style="left:778px;top:954px">Marriage Status: <span class="req">*</span></div>
<div class="abs field" style="left:133px;top:988px;width:288px"></div>
<div class="abs field" style="left:455px;top:988px;width:290px"></div>
<div class="abs field" style="left:778px;top:988px;width:289px">Single<svg width="14" height="9" viewBox="0 0 14 9"><path d="M1 1l6 6 6-6" fill="none" stroke="#666" stroke-width="1.6"/></svg></div>

<div class="abs label" style="left:133px;top:1050px">How Did You Hear About Us? <span class="req">*</span></div>
<div class="abs field" style="left:133px;top:1082px;width:560px">Please Select<svg width="14" height="9" viewBox="0 0 14 9"><path d="M1 1l6 6 6-6" fill="none" stroke="#666" stroke-width="1.6"/></svg></div>

<!-- Current address -->
<h2 class="abs section-title" style="left:132px;top:1170px">Current Address</h2>
<div class="abs section-rule" style="left:373px;top:1190px;width:694px"></div>
<div class="abs label" style="left:133px;top:1236px">Living Arrangements:</div>
<div class="abs label" style="left:455px;top:1236px">Post Code: <span class="req">*</span></div>
<div class="abs label" style="left:778px;top:1236px">Address: <span class="req">*</span></div>
<div class="abs field" style="left:133px;top:1269px;width:288px">Mr.</div>
<div class="abs field" style="left:455px;top:1269px;width:290px"></div>
<div class="abs field" style="left:778px;top:1269px;width:289px"></div>

<div class="abs label" style="left:133px;top:1331px">Time Spent At Address: <span class="req">*</span></div>
<div class="abs field" style="left:133px;top:1363px;width:111px"></div>
<div class="abs unit" style="left:257px;top:1374px">Years</div>
<div class="abs field" style="left:340px;top:1363px;width:110px"></div>
<div class="abs unit" style="left:464px;top:1374px">Months</div>

<!-- Primary employment -->
<h2 class="abs section-title" style="left:132px;top:1462px">Primary Employment Details</h2>
<div class="abs section-rule" style="left:526px;top:1482px;width:541px"></div>
<div class="abs label" style="left:133px;top:1529px">Employment Status:</div>
<div class="abs label" style="left:422px;top:1529px">Employment&nbsp; Name:</div>
<div class="abs label" style="left:738px;top:1529px">Employed For:</div>
<div class="abs field" style="left:133px;top:1561px;width:260px">Full Time<svg width="14" height="9" viewBox="0 0 14 9"><path d="M1 1l6 6 6-6" fill="none" stroke="#666" stroke-width="1.6"/></svg></div>
<div class="abs field" style="left:420px;top:1561px;width:290px"></div>
<div class="abs field" style="left:738px;top:1561px;width:103px"></div>
<div class="abs unit" style="left:851px;top:1571px">Years</div>
<div class="abs field" style="left:908px;top:1561px;width:94px"></div>
<div class="abs unit" style="left:1011px;top:1571px">Months</div>

<!-- Income & expenses -->
<h2 class="abs section-title" style="left:132px;top:1654px">Income &amp; Expenses</h2>
<div class="abs section-rule" style="left:415px;top:1674px;width:652px"></div>
<div class="abs label" style="left:133px;top:1712px">Employment Status:</div>
<div class="abs label" style="left:620px;top:1712px">Other Income:</div>
<div class="abs field" style="left:133px;top:1746px;width:260px"></div>
<div class="abs field" style="left:403px;top:1746px;width:178px">Weekly<svg width="14" height="9" viewBox="0 0 14 9"><path d="M1 1l6 6 6-6" fill="none" stroke="#666" stroke-width="1.6"/></svg></div>
<div class="abs field" style="left:620px;top:1746px;width:261px"></div>
<div class="abs field" style="left:891px;top:1746px;width:176px">Weekly<svg width="14" height="9" viewBox="0 0 14 9"><path d="M1 1l6 6 6-6" fill="none" stroke="#666" stroke-width="1.6"/></svg></div>

<div class="abs label" style="left:133px;top:1808px">Rent/Mortgage Payment:</div>
<div class="abs label" style="left:620px;top:1808px">Living / Other Expenses:</div>
<div class="abs field" style="left:133px;top:1840px;width:260px"></div>
<div class="abs field" style="left:403px;top:1840px;width:178px">Weekly<svg width="14" height="9" viewBox="0 0 14 9"><path d="M1 1l6 6 6-6" fill="none" stroke="#666" stroke-width="1.6"/></svg></div>
<div class="abs field" style="left:620px;top:1840px;width:261px"></div>
<div class="abs field" style="left:891px;top:1840px;width:176px">Weekly<svg width="14" height="9" viewBox="0 0 14 9"><path d="M1 1l6 6 6-6" fill="none" stroke="#666" stroke-width="1.6"/></svg></div>

<!-- Other -->
<h2 class="abs section-title" style="left:132px;top:1936px">Other</h2>
<div class="abs section-rule" style="left:225px;top:1956px;width:842px"></div>
<div class="abs label" style="left:133px;top:1994px">Deposit Amount $ (Optional)</div>
<div class="abs field" style="left:133px;top:2029px;width:466px">0</div>

<div class="abs agree">
  <span class="checkbox"><svg width="16" height="12" viewBox="0 0 16 12"><path d="M1.5 6l4.5 4.5L14.5 1.5" fill="none" stroke="#444" stroke-width="1.8"/></svg></span>
  <span>I'hv Read And Agree To The <a>Privacy Policy</a> And <a>Credit Guide Quote</a> <span class="req">*</span></span>
</div>
<div class="abs submit">SUBMIT</div>

<!-- Footer -->
<footer class="abs footer-info"></footer>
<div class="abs footer-icon" style="left:133px;top:2350px"><svg width="12" height="16" viewBox="0 0 12 16"><path d="M6 15C2 10 1 8 1 6a5 5 0 0 1 10 0c0 2-1 4-5 9z" fill="#fff"/><circle cx="6" cy="6" r="2" fill="#0255a3"/></svg></div>
<div class="abs" style="left:176px;top:2347px">
  <div class="footer-head">BRIGHTPATH FINANCE</div>
  <div class="footer-text">48 Harbour Lane, Eastwick NSW 2000</div>
</div>
<div class="abs footer-divider" style="left:524px;top:2319px"></div>
<div class="abs footer-icon" style="left:580px;top:2350px"><svg width="16" height="16" viewBox="0 0 20 20"><path d="M5 2l3 4-2 2c1 2 3 4 5 5l2-2 4 3-2 3C8 17 3 12 2 5z" fill="#fff"/></svg></div>
<div class="abs" style="left:625px;top:2347px">
  <div class="footer-head">CALL US</div>
  <div class="footer-text">1300 555 018</div>
</div>
<div class="abs footer-divider" style="left:787px;top:2319px"></div>
<div class="abs footer-icon" style="left:844px;top:2350px"><svg width="16" height="12" viewBox="0 0 16 12"><rect x="1" y="1" width="14" height="10" fill="#fff"/><path d="M1 1l7 6 7-6" fill="none" stroke="#0255a3" stroke-width="1.3"/></svg></div>
<div class="abs" style="left:889px;top:2347px">
  <div class="footer-head">EMAIL US</div>
  <div class="footer-text">info@brightpathfinance.example.com</div>
</div>

<div class="abs footer-bar"></div>
<nav class="abs footer-nav">
  <a>HOME</a><a>ABOUT</a><a>VEHICLE LOANS</a><a>OTHER LOANS</a><a>INSURANCE</a><a>FINANCE CALCULATOR</a><a>CONTACT</a>
</nav>
<div class="abs copyright">COPYRIGHT © 2016 BRIGHTPATH FINANCE. ALL RIGHTS RESERVED.</div>
<div class="abs social footer-social"><span></span><span></span><span></span></div>

</body>
</html>
```